I need a logo that demonstrates multiple of the same with one of a distinguishing feature. I would like something that can be recognisable in silhouette format. The business designs Management systems bespoke the to the company helping them pre-qualify for work.
Something that can demonstrate a distinction between a collective group non of which are the same in shape or size, with the largest of these not the distinguished object (or something to that effect).
This is a new business no logo or artwork exists.
Target Market(s)
Small to Medium Size enterprises in the city and rural areas. Looking to make the step up.
Industry/Entity Type
Manufacture
Contact Information for Business Card
room for, Name, Email, phone number
Font styles to use
Requirements
Must have
- would like the silhouette to be recognisable
Nice to have
- would like it to incorporate the name Keystone Advisory Frameworks.
- Would like the same logo to be on both business cards and on corporate shirts
Should not have
- anything that may exclude rural trade or manufacturing.
- I don't want to appear as corporate, just professional

```html
<!DOCTYPE html>
<html lang="en">
<head>
<meta charset="utf-8">
<title>Keystone Advisory Frameworks – Business Card</title>
<link href="https://fonts.googleapis.com/css2?family=Open+Sans:wght@400;600;700&display=swap" rel="stylesheet">
<style>
  :root {
    --backdrop: #9a9a9a;
    --card-black: #0d0d0d;
    --card-edge: #1c1c1c;
    --brand-red: #e0202a;
    --text-white: #f2f2f2;
    --text-grey: #9c9c9c;
    --rule: #2e2e2e;
  }
  * { margin: 0; padding: 0; box-sizing: border-box; }
  html, body { width: 1200px; height: 900px; overflow: hidden; }
  body {
    background: var(--backdrop);
    font-family: "Open Sans", Arial, sans-serif;
    position: relative;
  }
  .card {
    position: absolute;
    left: 285px;
    width: 630px;
    height: 360px;
    background: radial-gradient(ellipse at 40% 40%, var(--card-edge), var(--card-black) 75%);
    box-shadow: 0 10px 24px rgba(0,0,0,.35);
  }
  .card--front { top: 60px; display: flex; align-items: center; justify-content: center; }
  .card--back { top: 480px; }

  .front-wordmark {
    display: flex; align-items: center; gap: 16px;
    color: var(--text-white);
    font-weight: 700; font-size: 30px; letter-spacing: 1px;
  }
  .front-wordmark .mark-dot {
    width: 26px; height: 26px; border-radius: 50%; background: var(--text-white);
  }

  .holder { position: absolute; left: 48px; top: 118px; }
  .holder-name { color: var(--brand-red); font-weight: 700; font-size: 21px; line-height: 1.15; }
  .holder-role { color: var(--text-white); font-size: 14px; }

  .brand-wordmark {
    position: absolute; right: 44px; top: 100px;
    display: flex; align-items: center; gap: 10px;
    color: var(--brand-red); font-weight: 700; font-size: 22px; letter-spacing: .5px;
  }
  .brand-wordmark .mark-dot { width: 16px; height: 16px; border-radius: 50%; background: var(--brand-red); }

  .divider {
    position: absolute; left: 48px; right: 44px; top: 182px;
    height: 1px; background: var(--rule);
  }

  .contact-list {
    position: absolute; right: 44px; top: 214px;
    list-style: none; text-align: right;
  }
  .contact-list li {
    display: flex; justify-content: flex-end; align-items: center; gap: 10px;
    color: var(--text-white); font-size: 16px; line-height: 25px;
  }
  .contact-list svg { width: 13px; height: 13px; fill: none; stroke: var(--brand-red); stroke-width: 1.8; }
</style>
</head>
<body>

  <section class="card card--front">
    <div class="front-wordmark">
      <span class="mark-dot"></span>
      <span>Keystone Advisory Frameworks</span>
    </div>
  </section>

  <section class="card card--back">
    <div class="holder">
      <p class="holder-name">Daniel Hartley</p>
      <p class="holder-role">Managing Director</p>
    </div>

    <div class="brand-wordmark">
      <span class="mark-dot"></span>
      <span>Keystone Advisory Frameworks</span>
    </div>

    <div class="divider"></div>

    <ul class="contact-list">
      <li>555.010.2468
        <svg viewBox="0 0 14 14" aria-hidden="true"><rect x="3.5" y="1" width="7" height="12" rx="1.5"/><line x1="6" y1="11" x2="8" y2="11"/></svg>
      </li>
      <li>555.010.2468
        <svg viewBox="0 0 14 14" aria-hidden="true"><path d="M1.5 5c0-2 2-3 5.5-3s5.5 1 5.5 3l-2.5 1-1-1.5h-4l-1 1.5z"/><rect x="3" y="8" width="8" height="4.5" rx="1"/></svg>
      </li>
      <li>hello@keystoneaf.com
        <svg viewBox="0 0 14 14" aria-hidden="true"><rect x="1" y="3" width="12" height="8.5"/><path d="M1 3l6 5 6-5"/></svg>
      </li>
      <li>www.keystoneaf.com
        <svg viewBox="0 0 14 14" aria-hidden="true"><path d="M6 8.5l2.5-3"/><path d="M5.5 6L3.5 8a2 2 0 0 0 2.8 2.8l2-2"/><path d="M8.5 8l2-2A2 2 0 0 0 7.7 3.2l-2 2"/></svg>
      </li>
    </ul>
  </section>

</body>
</html>
```